Business Card Design Project : Ridgeline Press

In preparation for market launch, Tamarind's Ridgeline Press require the development of a business card. Ridgeline Press is a Community online publishing web portal. We provide the the city of Whistler located in B.C. (Canada) business directories, News, Classified ads, News, Events and blogs etc.

The main focus of the brand is to help local businesses to corporate with their online advertisement and marketing. Meeting our clients face to face is a must (B2B).

Target Market(s)

The target market is B2B customers. Business Owners to Marketing, advertising Managers

Industry/Entity Type

Business

Requirements
Must have
• - The business card will be two sided.
the BACK side will have our logo which consist of (icon, url,slogan) submited. The logo will be middle and centred.

The FRONT side should have company details:

Company Legal Name: TAMARIND RIDGELINE MEDIA

Owen Farsk
Director of Sales & Marketing

www.tamarindridgeline.biz
owen@tamarindridgeline.biz

Phone: 604 317 8842
#2714 - 582 E. Halvern St.
Vancouver, B.C. V7K2R4 Canada
Nice to have
• - For the "FRONT" side of our business card. You can separate or re-arrange with our logo components (icon, logo,slogan). It does not have to be together.

Also our company legal name is rather long so arrange or organize the name in a way to make it shorter. Your experience and creativity will have to come in play.
Should not have
• should not have other colors beside logo color and black text (2 colors). Also nothing Three dimensional

```html
<!DOCTYPE html>
<html lang="en">
<head>
<meta charset="utf-8">
<title>Ridgeline Press – Business Card</title>
<link rel="stylesheet" href="https://fonts.googleapis.com/css2?family=Open+Sans:wght@400;600;700&display=swap">
<style>
  :root {
    --brand-blue: #1f6fb5;
    --brand-blue-dark: #145a99;
    --ink: #111111;
    --paper: #ffffff;
    --backdrop: #e6e7e9;
  }
  * { box-sizing: border-box; margin: 0; padding: 0; }
  html, body { width: 1200px; height: 944px; overflow: hidden; }
  body {
    background: var(--backdrop);
    font-family: "Open Sans", Arial, sans-serif;
    position: relative;
  }
  .card {
    position: absolute;
    width: 600px;
    height: 340px;
    background: var(--paper);
    border-radius: 26px;
    overflow: hidden;
    box-shadow: 0 2px 10px rgba(0,0,0,0.12);
  }

  /* Back side */
  .card--back { left: 80px; top: 70px; }
  .back-content {
    position: absolute; inset: 0;
    display: flex; flex-direction: column; align-items: center; justify-content: center;
  }
  .brand-name {
    display: flex; align-items: center; gap: 14px;
    color: var(--brand-blue); font-weight: 700;
  }
  .brand-name__dot { width: 26px; height: 26px; border-radius: 50%; background: var(--brand-blue); }
  .card--back .brand-name { font-size: 46px; margin-bottom: 22px; }
  .back-url { font-size: 35px; font-weight: 700; color: var(--ink); letter-spacing: -0.3px; line-height: 1.1; }
  .back-slogan { font-size: 28px; color: var(--brand-blue); line-height: 1.2; margin-left: 110px; }

  /* Front side */
  .card--front { left: 520px; top: 520px; }
  .front-panel { position: absolute; inset: 0; }
  .front-logo { position: absolute; left: 44px; top: 34px; }
  .card--front .brand-name { font-size: 26px; gap: 10px; }
  .card--front .brand-name__dot { width: 16px; height: 16px; }
  .front-slogan { font-size: 17px; color: var(--brand-blue); margin-top: 4px; }
  .contact-list { position: absolute; left: 22px; top: 168px; list-style: none; }
  .contact-list li {
    display: flex; align-items: flex-start; gap: 8px;
    font-size: 15px; color: var(--ink); line-height: 1.3; margin-bottom: 6px;
  }
  .contact-list svg { flex: none; width: 14px; height: 14px; margin-top: 3px; fill: var(--brand-blue); }
  .holder {
    position: absolute; left: 420px; top: 150px; width: 180px; text-align: center;
    color: var(--paper);
  }
  .holder__name { font-size: 19px; font-weight: 600; }
  .holder__title { font-size: 12px; }
</style>
</head>
<body>

<section class="card card--back" aria-label="Business card back">
  <div class="back-content">
    <div class="brand-name"><span class="brand-name__dot"></span>Ridgeline Press</div>
    <div class="back-url">www.tamarindridgeline.biz</div>
    <div class="back-slogan">Your information gateway</div>
  </div>
</section>

<section class="card card--front" aria-label="Business card front">
  <svg class="front-panel" viewBox="0 0 600 340" preserveAspectRatio="none" aria-hidden="true">
    <defs>
      <linearGradient id="panelBlue" x1="0" y1="0" x2="1" y2="1">
        <stop offset="0" stop-color="#2a80c8"/>
        <stop offset="1" stop-color="#145a99"/>
      </linearGradient>
    </defs>
    <path d="M330 0 C 420 90, 420 250, 350 340 L 380 340 C 440 250, 440 90, 360 0 Z" fill="var(--ink)"/>
    <path d="M360 0 C 440 90, 440 250, 380 340 L 600 340 L 600 0 Z" fill="url(#panelBlue)"/>
  </svg>

  <div class="front-logo">
    <div class="brand-name"><span class="brand-name__dot"></span>Ridgeline Press</div>
    <div class="front-slogan">Your information gateway</div>
  </div>

  <ul class="contact-list">
    <li>
      <svg viewBox="0 0 16 16"><path d="M8 1 L15 8 H13 V15 H10 V10 H6 V15 H3 V8 H1 Z"/></svg>
      <span>#2714 - 582 E. Halvern St.<br>Vancouver, B.C. V7K2R4 Canada</span>
    </li>
    <li>
      <svg viewBox="0 0 16 16"><path d="M4 1 L7 4 L5 6 C6 8.5 7.5 10 10 11 L12 9 L15 12 L12 15 C6 14 2 10 1 4 Z"/></svg>
      <span>604 317 8842</span>
    </li>
    <li>
      <svg viewBox="0 0 16 16"><path d="M1 3 H15 V13 H1 Z M2 4 L8 9 L14 4" stroke="#fff" stroke-width="1"/></svg>
      <span>owen@tamarindridgeline.biz</span>
    </li>
    <li>
      <svg viewBox="0 0 16 16"><circle cx="8" cy="8" r="7"/></svg>
      <span>www.tamarindridgeline.biz</span>
    </li>
  </ul>

  <div class="holder">
    <div class="holder__name">Owen Farsk</div>
    <div class="holder__title">Director of Sales &amp; Marketing</div>
  </div>
</section>

</body>
</html>
```